Personal training and nutrition business needs business card design

We need a business card that outlays our services and invites potential customers to join our team and take the first step to a healthier and more enjoyable life. We cater for any level of fitness and specialize in weight loss and conditioning, strength training, muscle gain and strength endurance. Whether you are just starting off or need some help getting to the next level of your journey we are here to get the job done.
We specialize in one on one or one on two personal training sessions and each program will be custom made to suit individual fitness goals of our clients

```html
<!DOCTYPE html>
<html lang="en">
<head>
<meta charset="utf-8">
<title>Stride &amp; Core – Business Card</title>
<link href="https://fonts.googleapis.com/css2?family=Exo+2:ital,wght@0,700;1,800&family=Oswald:wght@500&family=Roboto:wght@400&display=swap" rel="stylesheet">
<style>
  :root{
    --backdrop:#2b2b2c;
    --card:#1b1b1c;
    --card-edge:#232324;
    --ink-dark:#3a3a3c;
    --white:#f2f2f2;
    --purple:#9b5aa8;
    --purple-deep:#6a44a0;
    --violet:#7d4fb3;
  }
  *{margin:0;padding:0;box-sizing:border-box}
  html,body{width:1200px;height:1138px;overflow:hidden;background:var(--backdrop)}
  .canvas{position:relative;width:1200px;height:1138px}
  .card{
    position:absolute;width:620px;height:374px;border-radius:16px;
    background:var(--card);overflow:hidden;
    box-shadow:0 4px 14px rgba(0,0,0,.35);
  }
  .card--front{left:274px;top:186px}
  .card--back{left:277px;top:608px}

  /* front */
  .front-brand{position:absolute;left:0;right:0;top:62px;text-align:center}
  .front-brand__dot{width:118px;height:118px;border-radius:50%;background:var(--card-edge);margin:0 auto 22px}
  .front-brand__name{
    font-family:"Exo 2",sans-serif;font-weight:700;font-size:46px;
    color:var(--ink-dark);letter-spacing:2px;
  }
  .tagline{
    font-family:"Oswald",sans-serif;font-weight:500;color:var(--purple);
    letter-spacing:1.2px;text-transform:uppercase;
  }
  .card--front .tagline{position:absolute;left:0;right:0;top:334px;text-align:center;font-size:13px}

  /* back */
  .accent-tab{position:absolute;right:-30px;top:44px;width:60px;height:60px;border-radius:50%;
    background:linear-gradient(180deg,var(--purple),var(--violet))}
  .bottom-bar{position:absolute;left:0;right:0;bottom:0;height:10px;
    background:linear-gradient(90deg,var(--purple),var(--purple-deep))}
  .person{position:absolute;right:37px;top:46px;text-align:right}
  .person__name{font-family:"Exo 2",sans-serif;font-style:italic;font-weight:800;font-size:27px;
    color:var(--violet);letter-spacing:1.5px}
  .person__role{font-family:"Roboto",sans-serif;font-size:16px;color:var(--white);margin-top:2px}

  .back-brand{position:absolute;left:37px;top:146px}
  .back-brand__dot{width:74px;height:74px;border-radius:50%;background:var(--purple);margin-left:40px;margin-bottom:22px}
  .back-brand__name{font-family:"Exo 2",sans-serif;font-weight:700;font-size:32px;line-height:32px;
    color:var(--white);letter-spacing:1px}
  .card--back .tagline{font-size:8px;margin-top:6px}

  .contact{position:absolute;right:37px;top:200px;font-family:"Roboto",sans-serif;font-size:16px;
    color:var(--white);text-align:right}
  .contact__address p{line-height:24px}
  .contact__list{list-style:none;margin-top:12px}
  .contact__list li{display:flex;justify-content:flex-end;align-items:center;height:24px;gap:12px}
  .contact__list svg{width:14px;height:14px;fill:var(--purple)}
</style>
</head>
<body>
<main class="canvas">

  <section class="card card--front" aria-label="Card front">
    <div class="front-brand">
      <div class="front-brand__dot"></div>
      <div class="front-brand__name">STRIDE &amp; CORE</div>
    </div>
    <p class="tagline">Personal training.&nbsp; Nutrition. Motivation</p>
  </section>

  <section class="card card--back" aria-label="Card back">
    <div class="accent-tab"></div>
    <div class="person">
      <h1 class="person__name">MARCUS REED</h1>
      <p class="person__role">Personal Trainer</p>
    </div>

    <div class="back-brand">
      <div class="back-brand__dot"></div>
      <div class="back-brand__name">STRIDE<br>&amp; CORE</div>
      <p class="tagline">Personal training.&nbsp; Nutrition. Motivation</p>
    </div>

    <div class="contact">
      <div class="contact__address">
        <p>1428 Cedar Ridge Lane</p>
        <p>Austin Texas 78701</p>
      </div>
      <ul class="contact__list">
        <li>+1 (512) 555-0147
          <svg viewBox="0 0 16 16" aria-hidden="true"><path d="M2 6c0-2 3-3 6-3s6 1 6 3v1h-3V5.5H5V7H2z"/><path d="M3 14l1-5h8l1 5z"/></svg></li>
        <li>marcus@stridencore.com
          <svg viewBox="0 0 16 16" aria-hidden="true"><path d="M1 3h14v10H1z M2.5 4.5 8 9l5.5-4.5" fill="none" stroke="#9b5aa8" stroke-width="1.6"/></svg></li>
        <li>www.stridencore.com
          <svg viewBox="0 0 16 16" aria-hidden="true"><circle cx="8" cy="8" r="6.5" fill="none" stroke="#9b5aa8" stroke-width="1.4"/><path d="M1.5 8h13M8 1.5c-3 3-3 10 0 13M8 1.5c3 3 3 10 0 13" fill="none" stroke="#9b5aa8" stroke-width="1.2"/></svg></li>
      </ul>
    </div>
    <div class="bottom-bar"></div>
  </section>

</main>
</body>
</html>
```